Stationery Design Project for Nimbora, Chicago

Nimbora, a street parking application which helps car drivers find a street parking spot by offering an ideal path along which to look for parking. This path is calculated by our algorithm based on data (e.g. historical data, baseball games schedule, etc.). Along this path the driver will find a spot and will also save 70% of the search time. Customer we target is reg. between 21 and 45 yo.

We envision something young, fresh, bright and original. Slightly abstract maybe. It should represent the idea and elements of finding street parking in the city, e.g. car(s), parking spot, people, city, etc. (just ideas!).

Logo is attached.

Requirement:
- Business Cards (2 Sided Full Color CMYK)
- Letterhead (1 Sided Full Color CMYK)
- Envelope (1 Sided Full Color CMYK)
- Sticker (1 Sided Full Color CMYK), round with a 2inch diameter.

Reason: We're starting to get more and more designs and need more time to look into all of them. Very exciting!! Thanks to everybody!

Hi all, we're in the process of selecting our favs. Though choices!!! Really good submissions. Will keep you posted and sorry for the delay.

Target Market(s)

Car drivers and owners between 21 and 45

Industry/Entity Type

Parking

Requirements
Must have
• Sticker should be round and include company URL nimbora.com and the new logo which we will attach soon.
Should not have
• Should not be too serious or boring.

```html
<!DOCTYPE html>
<html lang="en">
<head>
<meta charset="utf-8">
<title>Nimbora Business Card</title>
<link rel="stylesheet" href="https://fonts.googleapis.com/css2?family=Open+Sans:wght@400;600;700&display=swap">
<style>
  :root {
    --backdrop: #a88430;
    --card: #ffffff;
    --navy: #17237a;
    --royal: #2a4bb0;
    --cyan: #15b6ef;
    --band-dark: #111111;
    --band-mid: #5a5a5a;
    --ink: #2b2b2b;
    --wordmark: #1e1e1e;
    --icon: #1b8fd6;
    --mark: #1f55c8;
  }
  * { margin: 0; padding: 0; box-sizing: border-box; }
  html, body { width: 1200px; height: 686px; overflow: hidden; }
  body {
    background: var(--backdrop);
    font-family: "Open Sans", Arial, sans-serif;
    position: relative;
  }
  .card {
    position: absolute;
    width: 510px;
    height: 290px;
    background: var(--card);
    border-radius: 20px;
    overflow: hidden;
    box-shadow: 2px 2px 0 rgba(0,0,0,0.55);
  }
  .card--front { left: 73px; top: 130px; }
  .card--back  { left: 616px; top: 270px; }

  .swoosh { position: absolute; left: 0; top: 0; width: 510px; height: 290px; }

  .holder { position: absolute; right: 46px; top: 34px; text-align: right; color: #fff; }
  .holder__name { font-size: 17px; font-weight: 700; line-height: 1.2; }
  .holder__title { font-size: 13px; font-weight: 700; margin-top: 3px; }

  .brand { position: absolute; display: flex; align-items: center; }
  .brand__mark { border-radius: 50%; background: var(--mark); flex: none; }
  .brand__name { color: var(--wordmark); font-weight: 600; letter-spacing: -0.5px; line-height: 1; }

  .card--front .brand { left: 104px; top: 105px; }
  .card--front .brand__mark { width: 82px; height: 82px; margin-right: 12px; }
  .card--front .brand__name { font-size: 44px; }

  .card--back .brand { left: 59px; top: 99px; }
  .card--back .brand__mark { width: 110px; height: 110px; margin-right: 14px; }
  .card--back .brand__name { font-size: 58px; }

  .contact {
    position: absolute; left: 0; right: 38px; top: 212px;
    text-align: center; color: var(--ink); font-size: 12.5px; line-height: 21px;
  }
  .contact__row { display: flex; justify-content: center; gap: 16px; }
  .contact__item { display: inline-flex; align-items: center; gap: 3px; }
  .contact__item svg { width: 11px; height: 11px; fill: var(--icon); }
</style>
</head>
<body>

<section class="card card--front" aria-label="Business card front">
  <svg class="swoosh" viewBox="0 0 510 290" aria-hidden="true">
    <defs>
      <linearGradient id="band-blue" x1="0" y1="0" x2="1" y2="0">
        <stop offset="0" stop-color="var(--navy)"/>
        <stop offset="0.35" stop-color="var(--royal)"/>
        <stop offset="0.62" stop-color="var(--cyan)"/>
        <stop offset="0.85" stop-color="var(--royal)"/>
        <stop offset="1" stop-color="var(--navy)"/>
      </linearGradient>
      <linearGradient id="band-black" x1="0" y1="0" x2="1" y2="0">
        <stop offset="0" stop-color="var(--band-dark)"/>
        <stop offset="0.55" stop-color="var(--band-mid)"/>
        <stop offset="1" stop-color="var(--band-dark)"/>
      </linearGradient>
    </defs>
    <path d="M0,0 H510 V172 C360,72 185,22 0,38 Z" fill="url(#band-black)"/>
    <path d="M0,0 H510 V152 C360,58 185,16 0,31 Z" fill="#ffffff"/>
    <path d="M0,0 H510 V146 C360,52 185,11 0,26 Z" fill="url(#band-blue)"/>
  </svg>

  <div class="holder">
    <div class="holder__name">Your Name</div>
    <div class="holder__title">Title</div>
  </div>

  <div class="brand">
    <span class="brand__mark"></span>
    <span class="brand__name">Nimbora</span>
  </div>

  <div class="contact">
    <div>Street name City, State, zip code</div>
    <div class="contact__row">
      <span class="contact__item">
        <svg viewBox="0 0 24 24"><path d="M6.6 10.8a15 15 0 0 0 6.6 6.6l2.2-2.2a1 1 0 0 1 1-.25 11.4 11.4 0 0 0 3.6.57 1 1 0 0 1 1 1V20a1 1 0 0 1-1 1A17 17 0 0 1 3 4a1 1 0 0 1 1-1h3.5a1 1 0 0 1 1 1c0 1.25.2 2.45.57 3.57a1 1 0 0 1-.25 1z"/></svg>123-456-7890
      </span>
      <span class="contact__item">
        <svg viewBox="0 0 24 24"><path d="M6 2h9l3 3v5H6zM3 11h18v9H3zm3 3v2h4v-2zm0 3v1h12v-1z"/></svg>123-456-7890
      </span>
    </div>
    <div class="contact__row">
      <span class="contact__item">
        <svg viewBox="0 0 24 24"><path d="M2 5h20v14H2zm2 2v.5l8 5 8-5V7l-8 5z"/></svg>name@website.com
      </span>
      <span class="contact__item">
        <svg viewBox="0 0 24 24"><path d="M12 2a10 10 0 1 0 0 20 10 10 0 0 0 0-20zm-1 2.1V8H7.3A8 8 0 0 1 11 4.1zm2 0A8 8 0 0 1 16.7 8H13zM4.6 10H11v4H4.6a8 8 0 0 1 0-4zm8.4 0h6.4a8 8 0 0 1 0 4H13zm-5.7 6H11v3.9A8 8 0 0 1 7.3 16zm5.7 0h3.7A8 8 0 0 1 13 19.9z"/></svg>www.website.com
      </span>
    </div>
  </div>
</section>

<section class="card card--back" aria-label="Business card back">
  <div class="brand">
    <span class="brand__mark"></span>
    <span class="brand__name">Nimbora</span>
  </div>
</section>

</body>
</html>
```